New, modern business card for growing audiology practice

We need a new business card for our audiology practice. Our logo and website have recently changed (more modern) and we want our business cards to reflect this change.
We conduct hearing tests, perform earwax removals, and fit & dispense hearing aids to our patients. We are a family owned practice in which the owner is the one who works directly with the patient. I have attached logos in various formats to use, as well as two ideas I found on this website; as well as a scanned copy of our current logo. Good luck!

Industry/Entity Type

Business

Contact Information for Business Card

Company name: Tolvera Hearing Center
Provider name: Peter Wolstenby, Au.D. F/NSB
Phone number: (440) 683-5127
Address: 837 W. Lindell Ave. Marlow Heights, OH 44187
email: tolverahearing@postvane.com
website: tolverahearing.com

Colors
000000
aaaaaa
dbdbdb
cacaca
9bcb3c
afd23c
cadf82
b1b1b1

Requirements
Must have
• My card must include information in the "details" section. In the attached images, I found a few that I liked and I would like to model after - "brisky bouncin'" and "Sound Method Center".
• Must be horizontal.
• Must include logos provided. I uploaded them in various file formats and various ways.
• Must match logo font, if possible, if not, please get as close as you can.
Nice to have
• I really like the idea of having a color on one side with just the logo and company name and the contact information and provider name on the other side. I also really like the idea of having the main color dominating on the logo/company side with accent of that same color on the contact side of the card.
Should not have
• Must not be vertical.

```html
<!DOCTYPE html>
<html lang="en">
<head>
<meta charset="utf-8">
<title>Tolvera Hearing Center – Business Card</title>
<link rel="stylesheet" href="https://fonts.googleapis.com/css2?family=Lato:wght@400&family=Fjalla+One&family=Arimo:wght@400&display=swap">
<style>
  :root {
    --stage: #3a3a3a;
    --card: #1e1e1e;
    --green: #62a03a;
    --white: #f2f2f2;
    --grey: #cacaca;
  }
  * { box-sizing: border-box; margin: 0; padding: 0; }
  html, body { width: 799px; height: 1200px; overflow: hidden; }
  body {
    background: var(--stage);
    position: relative;
    font-family: "Arimo", Arial, sans-serif;
  }
  .card {
    position: absolute;
    left: 50px;
    width: 700px;
    height: 400px;
    background: var(--card);
    border-radius: 6px;
    overflow: hidden;
    box-shadow: 0 14px 30px rgba(0,0,0,.45);
  }
  .card--front { top: 130px; }
  .card--back { top: 680px; }

  /* Front */
  .brand-line {
    position: absolute;
    left: 70px;
    top: 150px;
    display: flex;
    align-items: center;
    gap: 16px;
  }
  .brand-dot {
    width: 26px; height: 26px;
    border-radius: 50%;
    background: var(--green);
  }
  .brand-name {
    font-family: "Lato", sans-serif;
    font-weight: 400;
    font-size: 38px;
    letter-spacing: 1px;
    color: var(--white);
    text-transform: uppercase;
  }
  .website {
    position: absolute;
    left: 100px;
    top: 250px;
    font-family: "Arimo", sans-serif;
    font-size: 19px;
    letter-spacing: 6px;
    color: var(--white);
  }
  .website .accent { color: var(--green); }

  /* Back */
  .stacked-brand {
    position: absolute;
    left: 70px;
    top: 40px;
    font-family: "Lato", sans-serif;
    font-weight: 400;
    color: var(--white);
    text-transform: uppercase;
    line-height: 1;
  }
  .stacked-brand .top { display: block; font-size: 44px; letter-spacing: 1px; }
  .stacked-brand .bottom { display: block; font-size: 22px; margin-top: 4px; }

  .provider {
    position: absolute;
    left: 40px;
    top: 150px;
  }
  .provider-name {
    font-family: "Fjalla One", sans-serif;
    font-size: 22px;
    color: var(--green);
  }
  .provider-role {
    font-size: 14px;
    color: var(--white);
    margin-top: 4px;
  }
  .contact-list {
    position: absolute;
    left: 40px;
    top: 222px;
    list-style: none;
    font-size: 17px;
    color: var(--white);
    line-height: 1.3;
  }
  .contact-list li {
    display: flex;
    align-items: flex-start;
    gap: 12px;
  }
  .contact-list svg { width: 14px; height: 14px; margin-top: 4px; flex: none; fill: var(--green); }

  .decor-circle {
    position: absolute;
    right: -70px;
    bottom: -90px;
    width: 360px;
    height: 360px;
    border-radius: 50%;
    background: var(--green);
  }
</style>
</head>
<body>

<section class="card card--front" aria-label="Card front">
  <div class="brand-line">
    <span class="brand-dot"></span>
    <span class="brand-name">Tolvera Hearing Center</span>
  </div>
  <p class="website">www.<span class="accent">tolverahearing</span>.com</p>
</section>

<section class="card card--back" aria-label="Card back">
  <h1 class="stacked-brand">
    <span class="top">Tolvera</span>
    <span class="bottom">Hearing Center</span>
  </h1>

  <div class="provider">
    <p class="provider-name">Peter Wolstenby, Au.D. F/NSB</p>
    <p class="provider-role">Owner - Audiologist</p>
  </div>

  <ul class="contact-list">
    <li>
      <svg viewBox="0 0 14 14" aria-hidden="true"><path d="M7 0a5 5 0 0 0-5 5c0 3.5 5 9 5 9s5-5.5 5-9a5 5 0 0 0-5-5zm0 7a2 2 0 1 1 0-4 2 2 0 0 1 0 4z"/></svg>
      <span>837 W. Lindell Ave.<br>Marlow Heights, OH 44187</span>
    </li>
    <li>
      <svg viewBox="0 0 14 14" aria-hidden="true"><path d="M3 1l2.5 3-1.5 1.5a8 8 0 0 0 4.5 4.5L10 8.5l3 2.5-1.5 2.5C6 13 1 8 .5 2.5z"/></svg>
      <span>(440) 683-5127</span>
    </li>
    <li>
      <svg viewBox="0 0 14 14" aria-hidden="true"><path d="M0 2h14v10H0zM1.5 3.2 7 7.5l5.5-4.3z" fill-rule="evenodd"/></svg>
      <span>tolverahearing@postvane.com</span>
    </li>
    <li>
      <svg viewBox="0 0 14 14" aria-hidden="true"><circle cx="7" cy="7" r="6.5"/></svg>
      <span>www.tolverahearing.com</span>
    </li>
  </ul>

  <div class="decor-circle" aria-hidden="true"></div>
</section>

</body>
</html>
```